Women's Uplift & Praise Luncheon - Matching Poster, flyer and Postcard

We are a Christian Event & Travel Company and we are hosting our inaugural event on June 10, 2017. This event is a Women's Uplift & Praise Luncheon aboard a private yacht leaving out of Crescent Landing, Maryland. The event will cater to women who have a vision to start or have already embarked on the journey of starting or growing a business or ministry. The event calls for a matching poster, flyer and postcard design that give an elegant & exquisite feel with just the right breath of freshness. The colors should reflect our logo as this is our launch event. I have also included 2 photos of the Islandsong Heritage Park production (one of our sponsors) - Please include but do not make it take over the design - this is to advertise the door prize. The final design will portray the branding of the company (Christian, travel, events, elegance, professional), the branding of the event (elegant and luxurious) and the importance of this launch event.
Please include the following information:
Lanternway Event & Travel Group presents
Event name: Rising Tide: Grace, Patience & Devotion.
Tag Line/Description: An Exquisite Women's Uplift & Praise Luncheon.
Guest Speaker: Minister Harriet L. Dunmore (Photo included)
VP of Pinecrest Bank
Asst. Pastor & First Lady of Bethany Grove Baptist Church
Special Guest Psalmist: Minister Tasha Bellamy (Photo Included)
Worship Director of Stillmeadow Community Church
Vocalist, Songwriter, Musician, and Clinician
Venue: Aboard the Sovereign Pearl Yacht
Dock: Crescent Landing
512 Marlowe Quay, Fenwick, MD 20999
Boarding 10:00am
Sailing Promptly at 10:30am
(Please be on time the yacht will not wait)
Date: Saturday June 10, 2017
Tickets: Early Bird US$75.00/person (ends May 15, 2017)
Regular Tickets US$95.99
Purchase Tickets at www.lanternwayevent-travel.example/rising-tide
SPACE IS LIMITED DUE TO YACHT CAPACITY
Grand Prize: Vivienne Laroux Purse
Door Prize: 2 Tickets to the Hawaiian Islandsong Heritage Park
Other prizes for special ladies in attendance.
Ladies are asked to dress in Elegant White Ensemble
Corporate Sponsors:
The Islandsong Heritage Park (Logo included)
J. Ramsey Photography (Logo included)
Special Thanks to our Individual Sponsors:
Mrs. L. Garner, Mr. R Fielding & Mr. T. Ogden

Target Market(s)

Women, Business, Ministry, Christians, Middle to Upper Class

Industry/Entity Type

Events

Font styles to use
Serif
Script

Requirements
Must have
• Elegance, professional, vivid in color & font. be creative in Visual and FONT!
• Poster: 18" X 24"
• Flyer: one sided.
• ***** the final design chosen will have a cross referenced design of 1 flyer, 1 postcard 1 poster. This was included so you have a reference - Be creative!!!!!!
Nice to have
• Matching across all 3 designs (poster, flyer & postcard) but sized appropriately and just enough difference to play up the design and be appealing.
• I uploaded 3 example flyers to give you inspiration of the type of visuals I'm looking for. I removed my amateur sample because the designs were copying it instead of being creative.
Should not have
• Any thing inappropriate, alcohol oriented or sexual

```html
<!DOCTYPE html>
<html lang="en">
<head>
<meta charset="utf-8">
<title>Rising Tide – Women's Uplift & Praise Luncheon</title>
<link rel="stylesheet" href="https://fonts.googleapis.com/css2?family=Alfa+Slab+One&family=Kalam:wght@400;700&family=Marck+Script&family=Tinos:wght@400;700&family=Oswald:wght@300&display=swap">
<style>
  :root {
    --wine-deep: #2a0a06;
    --wine-mid: #6e1a0c;
    --ember: #a8320f;
    --gold: #f2c94c;
    --gold-light: #ffe28a;
    --gold-dark: #b4841c;
    --sea: #3f9fb9;
    --sea-top: #46a9c3;
    --sea-deep: #1f6f88;
    --ink: #0f2630;
    --cream: #f5efe6;
    --white: #ffffff;
  }
  * { box-sizing: border-box; margin: 0; padding: 0; }
  html, body { width: 900px; height: 1200px; overflow: hidden; background: #222; }
  .poster {
    position: relative; width: 900px; height: 1200px; overflow: hidden;
    background: radial-gradient(ellipse at 50% 40%, var(--ember) 0%, var(--wine-mid) 40%, var(--wine-deep) 100%);
    font-family: "Tinos", serif;
  }
  .abs { position: absolute; white-space: nowrap; }
  .center { left: 0; width: 900px; text-align: center; }
  .silhouette {
    left: 300px; top: 0; width: 300px; height: 680px;
    background: linear-gradient(180deg, rgba(20,5,3,0.75), rgba(30,8,4,0.55) 60%, rgba(30,8,4,0));
    border-radius: 0 0 45% 45%;
  }
  .corner-band {
    left: -70px; top: 30px; width: 240px; height: 44px;
    background: #2aa3c4; transform: rotate(-45deg);
    color: var(--ink); font: 700 18px "Tinos", serif; line-height: 44px; text-align: center;
  }
  .brand-ring {
    left: 375px; top: 10px; width: 150px; height: 150px; border-radius: 50%;
    border: 3px solid var(--gold);
  }
  .brand {
    left: 375px; top: 42px; width: 150px; text-align: center;
    color: var(--gold); font: 700 23px/1.15 "Tinos", serif;
  }
  .brand small { display: block; font-size: 12px; letter-spacing: 0.5px; margin-top: 4px; }
  .presents { top: 166px; color: var(--gold); font: 400 25px/32px "Kalam", cursive; }
  .title {
    top: 190px; font: 66px/72px "Alfa Slab One", serif; letter-spacing: 2px;
    background: linear-gradient(180deg, var(--gold-light) 0%, var(--gold) 45%, var(--gold-dark) 100%);
    -webkit-background-clip: text; background-clip: text; color: transparent;
    text-shadow: 0 3px 4px rgba(0,0,0,0.35);
  }
  .virtues {
    right: 118px; top: 255px; color: var(--gold);
    font: 400 20px/22px "Tinos", serif; letter-spacing: 0.5px;
  }
  .tagline { top: 283px; color: var(--gold); font: 400 30px/36px "Kalam", cursive; }
  .portrait { border-radius: 40% 40% 10% 10%; }
  .portrait-left { left: 40px; top: 330px; width: 150px; height: 200px; background: linear-gradient(160deg, #3b1810, #c62a22 70%, #8a1b14); }
  .portrait-right { left: 714px; top: 325px; width: 150px; height: 205px; background: linear-gradient(160deg, #1c0d08, #6a3a28 50%, #e8e2d8); }
  .caption { color: var(--cream); font: 400 15.5px/19.5px "Tinos", serif; text-align: center; }
  .caption b { font-weight: 700; }
  .caption-left { left: 5px; top: 537px; width: 230px; }
  .caption-right { left: 655px; top: 535px; width: 250px; }
  .details { color: var(--gold); font-family: "Marck Script", cursive; }
  .venue { top: 388px; font-size: 27px; line-height: 32px; }
  .dock { top: 430px; font: italic 19px/22px "Tinos", serif; letter-spacing: 0.5px; color: var(--gold); }
  .address { top: 461px; font-size: 22.5px; line-height: 26px; }
  .boarding { top: 503px; font-size: 25px; line-height: 29px; }
  .boarding .note { font-size: 22px; }
  .date { top: 604px; font-size: 31px; line-height: 34px; }
  .sea {
    left: 0; top: 670px; width: 900px; height: 530px;
    background: linear-gradient(180deg, var(--sea-top) 0%, var(--sea) 45%, var(--sea-deep) 100%);
  }
  .wave { position: absolute; top: -18px; left: 0; }
  .photo { border-radius: 6px; box-shadow: 0 3px 8px rgba(0,0,0,0.5); }
  .photo-left { left: 22px; top: 707px; width: 216px; height: 140px; background: linear-gradient(160deg, #3a2a12, #b89a3c 55%, #3e6a28); }
  .photo-right { left: 665px; top: 707px; width: 216px; height: 140px; background: radial-gradient(circle at 50% 50%, #f08a20, #5a2408 45%, #0a0704 80%); }
  .ticket { color: var(--ink); font-family: "Marck Script", cursive; }
  .price { font-size: 27px; line-height: 30px; }
  .price-regular { font-size: 29px; }
  .small-note { font-size: 15px; line-height: 18px; }
  .buy { font: 300 17px/20px "Oswald", sans-serif; color: var(--ink); }
  .url { font: 400 18px/21px "Tinos", serif; color: var(--ink); letter-spacing: -0.3px; }
  .limited { font: italic 14.5px/18px "Tinos", serif; color: var(--ink); letter-spacing: 0.5px; }
  .prize { font-size: 21px; line-height: 24px; }
  .dress { color: var(--white); font-size: 22px; line-height: 26px; text-shadow: 0 1px 3px rgba(0,0,0,0.45); }
  .sponsor-panel {
    left: 192px; top: 994px; width: 520px; height: 186px;
    background: rgba(255,255,255,0.16); border-radius: 8px;
  }
  .sponsor-head { left: 192px; width: 520px; text-align: center; top: 995px; font: 300 20px/24px "Oswald", sans-serif; letter-spacing: 3px; color: var(--ink); }
  .sponsor-card {
    top: 1028px; height: 78px; background: var(--white); border-radius: 5px;
    display: flex; align-items: center; justify-content: center; text-align: center;
    color: var(--gold-dark); font: 700 15px/1.2 "Tinos", serif; padding: 6px; white-space: normal;
  }
  .card-photo { left: 314px; width: 86px; font-size: 12px; }
  .card-park { left: 408px; width: 174px; }
  .thanks { left: 192px; width: 520px; text-align: center; top: 1113px; font-size: 24px; line-height: 30px; color: var(--ink); }
</style>
</head>
<body>
<main class="poster">
  <div class="abs silhouette" role="img" aria-label="Dark silhouette of a woman in a flowing gown"></div>

  <div class="abs corner-band">Limited Tickets</div>

  <div class="abs brand-ring"></div>
  <div class="abs brand">Lanternway<small>Event &amp; Travel Group</small></div>

  <p class="abs center presents">Presents</p>
  <h1 class="abs center title">RISING TIDE</h1>
  <p class="abs virtues">GRACE ~ PATIENCE ~ DEVOTION</p>
  <p class="abs center tagline">An Exquisite Women's Uplift<br>&amp; Praise Luncheon</p>

  <div class="abs portrait portrait-left" role="img" aria-label="Portrait of guest speaker Minister Harriet L. Dunmore"></div>
  <p class="abs caption caption-left">Guest Speaker<br><b>Minister Harriet L. Dunmore</b><br>VP of Pinecrest Bank<br>Asst. Pastor &amp; First Lady of<br>Bethany Grove Baptist Church</p>

  <div class="abs portrait portrait-right" role="img" aria-label="Portrait of special guest psalmist Minister Tasha Bellamy"></div>
  <p class="abs caption caption-right">Special Guest Psalmist<br><b>Minister Tasha Bellamy</b><br>Worship Director of Stillmeadow<br>Community Church<br>Vocalist, Songwriter, Musician<br>and Clinician</p>

  <p class="abs center details venue">Venue : Aboard the Sovereign Pearl Yacht</p>
  <p class="abs center dock">DOCK : CRESCENT LANDING</p>
  <p class="abs center details address">512 Marlowe Quay, Fenwick, MD 20999</p>
  <p class="abs center details boarding">Boarding: 10:00 am<br>Sailing Promptly at: 10:30 am<br><span class="note">(Please be on time the yacht will not wait)</span></p>
  <p class="abs center details date">Saturday&nbsp; 10th June 2017</p>

  <div class="abs sea">
    <svg class="wave" width="900" height="40" viewBox="0 0 900 40" aria-hidden="true">
      <path d="M0 22 C150 8 300 30 450 18 C600 6 750 28 900 14 L900 40 L0 40 Z" fill="#46a9c3"/>
    </svg>
  </div>

  <div class="abs photo photo-left" role="img" aria-label="Island dancers in grass skirts performing on stage"></div>
  <div class="abs photo photo-right" role="img" aria-label="Fire knife dancers spinning flaming batons at night"></div>

  <p class="abs center ticket price" style="top:692px">Early Bird: $75 /Person</p>
  <p class="abs center ticket small-note" style="top:723px">Early Birds ends 15th May&nbsp; 2017</p>
  <p class="abs center ticket price price-regular" style="top:749px">Regular Tickets: $95.99 /Person</p>
  <p class="abs center buy" style="top:778px">Purchase Tickets at</p>
  <p class="abs center url" style="top:800px">www.lanternwayevent-travel.example/rising-tide</p>
  <p class="abs center limited" style="top:826px">SPACE IS LIMITED DUE TO YACHT CAPACITY</p>
  <p class="abs center ticket prize" style="top:850px">Grand Prize: Vivienne Laroux Purse</p>
  <p class="abs center ticket prize" style="top:876px">Door Prize: 2 Tickets to the Hawaiian Islandsong Heritage Park</p>
  <p class="abs center ticket prize" style="top:902px">Other prizes for special ladies in attendance</p>
  <p class="abs center ticket dress" style="top:931px">Ladies are asked to dress in Elegant White Ensembles</p>
  <p class="abs center ticket prize" style="top:961px">Tickets on Sale&nbsp; 18th March 2017</p>

  <div class="abs sponsor-panel"></div>
  <p class="abs sponsor-head">CORPORATE SPONSORS</p>
  <div class="abs sponsor-card card-photo">J. Ramsey Photography</div>
  <div class="abs sponsor-card card-park">Islandsong Heritage Park</div>
  <p class="abs ticket thanks">Special Thanks to our Individual Sponsors<br>Mrs. L. Garner, Mr. R Fielding and Mr. T. Ogden</p>
</main>
</body>
</html>
```